Actors Postcard Design

I need a postcard designed for me. I am an actor, voice over artist and technical adviser for tv, film and videogames. I am open to color ideas. My photos are in black and white so something to make those stand out a bit. Masculine colors like dark blue etc..I have seen some of your designs with 3 photos which I liked. Perhaps a 2-3 photo scheme. Back of postcard to contain my resume. Want it to look professional and not cartoonish (since I mentioned video games). Front to have photos and job title and contact info
Updates

Please take my color direction lightly, I am open to all color schemes. light or dark. You are the professionals. Am looking forward to seeing what all of you come up with. Thanks

Industry/Entity Type

Tv

```html
<!DOCTYPE html>
<html lang="en">
<head>
<meta charset="utf-8">
<title>Actor Postcard – Back</title>
<link rel="stylesheet" href="https://fonts.googleapis.com/css2?family=Didact+Gothic&family=Mulish:wght@800&display=swap">
<style>
  :root {
    --backdrop: #767272;
    --card: #ffffff;
    --accent: #1ba6e1;
    --ink: #1f1f1f;
    --rule: #555555;
  }
  * { margin: 0; padding: 0; box-sizing: border-box; }
  html, body { width: 1200px; height: 938px; overflow: hidden; }
  body { background: var(--backdrop); position: relative; font-family: "Didact Gothic", sans-serif; color: var(--ink); }
  .postcard { position: absolute; left: 87px; top: 74px; width: 1026px; height: 789px; background: var(--card); }
  .resume-title { position: absolute; left: 43px; top: 38px; font-family: "Mulish", sans-serif; font-weight: 800; font-size: 27px; color: var(--accent); }
  .section { position: absolute; left: 30px; width: 480px; }
  .section-icon { position: absolute; left: 0; top: 0; }
  .section-head { position: absolute; left: 71px; top: 0; right: 0; display: flex; align-items: center; gap: 12px; height: 26px; }
  .section-head h2 { font-family: "Mulish", sans-serif; font-weight: 800; font-size: 17px; white-space: nowrap; }
  .section-head .bar { flex: 1; height: 5px; background: var(--accent); }
  .section-body { position: absolute; left: 71px; top: 26px; font-size: 19px; line-height: 26px; white-space: nowrap; word-spacing: -1px; }
  .voice-list { display: grid; grid-template-columns: 112px 18px auto; }
  .gap-top { margin-top: 8px; }
  .stamp-box { position: absolute; left: 860px; top: 30px; width: 125px; height: 149px; border: 1px solid var(--rule); }
  .address-line { position: absolute; left: 654px; width: 321px; height: 1px; background: var(--rule); }
</style>
</head>
<body>
<div class="postcard">
  <h1 class="resume-title">TRAINING/EXPERIENCE</h1>

  <section class="section" style="top:84px;">
    <svg class="section-icon" viewBox="0 0 48 48" width="48" height="48" style="top:4px;" aria-hidden="true">
      <g fill="none" stroke="#1ba6e1" stroke-width="3">
        <rect x="15" y="18" width="30" height="26" rx="2"/>
        <path d="M15 12 L43 6 L44 12 L16 18 Z"/>
      </g>
      <path d="M26 24 L36 31 L26 38 Z" fill="#1ba6e1"/>
      <rect x="15" y="18" width="30" height="5" fill="#1ba6e1"/>
    </svg>
    <div class="section-head"><h2>Acting</h2><span class="bar"></span></div>
    <div class="section-body">
      <p>Marlow Hale Acting School - 1.5 yrs2</p>
      <p>Screen Craft International – On Camera 2yrs</p>
      <p>NCA North Coast Acting – 5 day intensive</p>
    </div>
  </section>

  <section class="section" style="top:202px;">
    <svg class="section-icon" viewBox="0 0 48 90" width="48" height="86" style="top:8px;" aria-hidden="true">
      <circle cx="36" cy="14" r="11" fill="#1ba6e1"/>
      <path d="M28 22 L12 50 L17 54 L34 26 Z" fill="#1ba6e1"/>
      <path d="M13 52 C4 60 2 70 6 74 C9 77 14 74 12 70" fill="none" stroke="#1ba6e1" stroke-width="3"/>
    </svg>
    <div class="section-head"><h2>Voice Over</h2><span class="bar"></span></div>
    <div class="section-body voice-list">
      <span>Voice Forge</span><span>-</span><span>Daytime Conservatory</span>
      <span></span><span></span><span>(commercial, narration, etc…)</span>
      <span></span><span>-</span><span>Adv Daytime Conservatory</span>
      <span></span><span>-</span><span>4 day Character Intensive</span>
    </div>
  </section>

  <section class="section" style="top:347px;">
    <svg class="section-icon" viewBox="0 0 52 52" width="52" height="52" style="top:0;" aria-hidden="true">
      <path d="M40 4 L48 12 L24 36 L16 28 Z" fill="#1ba6e1"/>
      <path d="M16 30 L6 44 L10 48 L22 36 Z" fill="#1ba6e1"/>
      <path d="M6 10 C6 4 12 2 16 4 L12 9 L15 12 L20 8 C22 12 20 18 14 18 L44 46 L40 50 L11 21 C6 20 4 14 6 10 Z" fill="#1ba6e1"/>
    </svg>
    <div class="section-head"><h2>Technical Advising</h2><span class="bar"></span></div>
    <div class="section-body">
      <p>Federal Special Agent – 10.5 yrs</p>
      <p class="gap-top">Extensive Firearms Training – Agency, Ironside Tactics,</p>
      <p>Former Talon Members, Army Recon. Defensive</p>
      <p>Tactics, Breaching, Vehicle Containment,</p>
      <p>Surveillance, etc…</p>
    </div>
  </section>

  <section class="section" style="top:526px;">
    <svg class="section-icon" viewBox="0 0 52 56" width="52" height="56" style="top:-12px;" aria-hidden="true">
      <path d="M44 2 L46 7 L51 7 L47 10 L49 15 L44 12 L39 15 L41 10 L37 7 L42 7 Z" fill="#1ba6e1"/>
      <circle cx="22" cy="30" r="15" fill="none" stroke="#1ba6e1" stroke-width="4"/>
      <circle cx="22" cy="26" r="5" fill="#1ba6e1"/>
      <path d="M13 38 C14 32 30 32 31 38 Z" fill="#1ba6e1"/>
      <path d="M33 41 L44 52" stroke="#1ba6e1" stroke-width="6" stroke-linecap="round"/>
    </svg>
    <div class="section-head"><h2>Special Skills</h2><span class="bar"></span></div>
    <div class="section-body">
      <p>15 yrs martial arts (Gung Fu, Judo, Tai Chi,</p>
      <p>Kenjutsu), EMT, Personal Trainer, Scuba,</p>
      <p>Snowboarding, Snowshoeing, Alpine</p>
      <p>Mountaineering, Archery, Mountainbiking, SUP,</p>
      <p>Blacksmithing, Carpentry 7yrs. Fluent Polish.</p>
    </div>
  </section>

  <div class="stamp-box"></div>
  <div class="address-line" style="top:369px;"></div>
  <div class="address-line" style="top:449px;"></div>
  <div class="address-line" style="top:530px;"></div>
</div>
</body>
</html>
```